Letter design, envelope design, and more

Hello, we the Tavrin Gmbh are looking for our shop. Letter C5. Design does not have to be like a business card, so it can have straight lines. Only the color is important. The logo is the text under TaVRin omit.It should not be playful but Profesionel

Font styles to use
Sans Serif

Colors
0555a3
3176b5
85abd2
85cae6
34a7d8
0792cd
cee9f5
cfdfed
000000

Requirements
Must have
• Color like business card, Please, with the text under TaVRin, Correct address Lindmattstr. 4 Zip code 9517 Goldach, as well as Couvert Without addressing only design and logo with TaVrn
Nice to have
• more writing articles
Should not have
• Not too colored, Text under TaVRin, bright colors

```html
<!DOCTYPE html>
<html lang="en">
<head>
<meta charset="utf-8">
<title>TaVRin Gmbh – Letterhead</title>
<link rel="stylesheet" href="https://fonts.googleapis.com/css2?family=Source+Sans+3:wght@400;600&display=swap">
<style>
  :root {
    --backdrop: #b2b2b2;
    --paper: #f1f1f1;
    --ink: #1f1f1f;
    --blue-deep: #0555a3;
    --blue-mid: #3176b5;
    --blue-light: #85abd2;
    --white: #ffffff;
  }
  * { margin: 0; padding: 0; box-sizing: border-box; }
  html, body { width: 1200px; height: 1072px; overflow: hidden; }
  body {
    position: relative;
    background: var(--backdrop);
    font-family: "Source Sans 3", sans-serif;
    color: var(--ink);
  }
  .sheet {
    position: absolute;
    width: 548px; height: 772px;
    background: var(--paper);
    overflow: hidden;
  }
  .sheet-follow { left: 371px; top: 192px; }
  .sheet-front { left: 301px; top: 101px; }

  .header-waves { position: absolute; left: 0; top: 0; width: 548px; height: 160px; }
  .web-address {
    position: absolute; right: 22px; top: 33px;
    font-size: 14px; color: var(--white); letter-spacing: 2.4px;
  }
  .brand {
    position: absolute; left: 26px; top: 32px;
    display: flex; align-items: center; gap: 8px;
  }
  .brand-square { width: 20px; height: 20px; background: var(--blue-deep); }
  .brand-name {
    font-size: 30px; font-weight: 600; color: var(--blue-deep);
    letter-spacing: 0.5px; line-height: 1;
  }

  .letter-body {
    position: absolute; left: 76px; top: 186px; width: 404px;
    font-size: 12.2px; line-height: 16.9px;
  }
  .salutation { font-size: 14.6px; line-height: 20px; margin-bottom: 32px; }
  .letter-body p.text { margin-bottom: 16.9px; }
  .signature { margin-top: 34px; }

  .footer-rule {
    position: absolute; left: 12px; top: 739px;
    width: 519px; height: 1.3px; background: var(--blue-deep);
  }
  .contact-line {
    position: absolute; top: 746px; left: 0; width: 548px; height: 20px;
    font-size: 10.4px; color: var(--blue-deep);
  }
  .contact-item { position: absolute; display: flex; align-items: center; gap: 4px; height: 20px; white-space: nowrap; }
  .contact-item svg { width: 15px; height: 15px; }
  .contact-phone { left: 74px; }
  .contact-mail { left: 213px; }
  .contact-address { left: 337px; }
  .divider { display: inline-block; width: 1px; height: 12px; background: var(--blue-deep); margin: 0 4px; vertical-align: middle; }
</style>
</head>
<body>
  <!-- follow-up sheet -->
  <section class="sheet sheet-follow">
    <svg class="header-waves" viewBox="0 0 548 160" aria-hidden="true">
      <path fill="var(--blue-light)" d="M198,0 C240,72 305,88 400,100 C470,110 520,120 548,142 L548,0 Z"/>
      <path fill="var(--blue-mid)" d="M198,0 C236,66 300,80 400,92 C470,100 520,108 548,127 L548,0 Z"/>
      <path fill="var(--blue-deep)" d="M198,0 C230,58 290,75 380,82 C460,88 520,90 548,108 L548,0 Z"/>
    </svg>
    <div class="web-address">www.tavrin.ch</div>
    <div class="footer-rule"></div>
    <footer class="contact-line">
      <div class="contact-item contact-phone">
        <svg viewBox="0 0 20 20" aria-hidden="true"><circle cx="10" cy="10" r="8.5" fill="none" stroke="var(--blue-deep)" stroke-width="1"/><path d="M7 6 L8.5 6 L9.2 8 L8.2 8.8 C8.8 10.2 9.8 11.2 11.2 11.8 L12 10.8 L14 11.5 L14 13 C10 13.5 6.5 10 7 6 Z" fill="none" stroke="var(--blue-deep)" stroke-width="0.9"/></svg>
        <span>+41 71 555 20 40</span>
      </div>
      <div class="contact-item contact-mail">
        <svg viewBox="0 0 20 20" aria-hidden="true"><circle cx="10" cy="10" r="8.5" fill="none" stroke="var(--blue-deep)" stroke-width="1"/><path d="M5.5 10 L14.5 6 L12 14.5 L9.5 11 Z M9.5 11 L14.5 6" fill="none" stroke="var(--blue-deep)" stroke-width="0.9" stroke-linejoin="round"/></svg>
        <span>info@tavrin.ch</span>
      </div>
      <div class="contact-item contact-address">
        <svg viewBox="0 0 20 20" aria-hidden="true"><circle cx="10" cy="10" r="8.5" fill="none" stroke="var(--blue-deep)" stroke-width="1"/><path d="M10 15 C8 12 6.8 10.3 6.8 8.6 A3.2 3.2 0 0 1 13.2 8.6 C13.2 10.3 12 12 10 15 Z" fill="none" stroke="var(--blue-deep)" stroke-width="0.9"/><circle cx="10" cy="8.6" r="1.1" fill="var(--blue-deep)"/></svg>
        <span>Lindmattstr. 4<span class="divider"></span>9517 Goldach</span>
      </div>
    </footer>
  </section>

  <!-- first sheet -->
  <main class="sheet sheet-front">
    <svg class="header-waves" viewBox="0 0 548 160" aria-hidden="true">
      <path fill="var(--blue-light)" d="M198,0 C240,72 305,88 400,100 C470,110 520,120 548,142 L548,0 Z"/>
      <path fill="var(--blue-mid)" d="M198,0 C236,66 300,80 400,92 C470,100 520,108 548,127 L548,0 Z"/>
      <path fill="var(--blue-deep)" d="M198,0 C230,58 290,75 380,82 C460,88 520,90 548,108 L548,0 Z"/>
    </svg>

    <div class="brand">
      <span class="brand-square"></span>
      <span class="brand-name">TaVRin</span>
    </div>
    <div class="web-address">www.tavrin.ch</div>

    <section class="letter-body">
      <p class="salutation">Dear Mr. Smith,</p>
      <p class="text">Lorem ipsum dolor sit amet, consectetur adipiscing elit. Donec orci purus, luctus vitae dignissim eu, iaculis sed purus. Vivamus faucibus, ipsum nec aliquet viverra, leo mauris condimentum ligula, sit amet sagittis enim ligula quis arcu. Nam egestas tortor id nisi porttitor mattis. In tortor ante, ultricies in suscipit a, tempus non massa. Vivamus et auctor mi. Fusce vel massa nulla. Phasellus nec eros mauris, et scelerisque orci. Donec malesuada orci vitae nulla accumsan porta a id massa. Quisque accumsan iaculis magna sit amet fringilla. Maecenas consequat, magna eget tincidunt semper, odio nibh rutrum mi, id feugiat ante nisi eu risus. Vestibulum nunc orci, rhoncus a placerat in, ultricies in mi. Cras mattis varius eros, vel fringilla nisi suscipit eget.</p>
      <p class="text">Quisque scelerisque sagittis nulla at porttitor. Mauris a justo et tellus interdum tristique. Sed id augue vitae urna euismod commodo aliquet a quam. Pellentesque arcu velit, cursus et malesuada ut, consequat et diam. Nullam erat sem, rhoncus id ullamcorper vitae, rhoncus et arcu. In ultricies ultricies nulla, ut rutrum nisi iaculis at. Donec eu magna a metus ornare faucibus. Fusce aliquet faucibus ultricies. Morbi semper, est id tincidunt gravida, sem arcu adipiscing lacus, ac bibendum nulla leo eu purus. Quisque nec diam sed risus consectetur a ccumsan quis quis nibh. Vestibulum id purus lorem.</p>
      <p class="signature">John Doe<br>Co-Founder &amp; CEO</p>
    </section>

    <div class="footer-rule"></div>
    <footer class="contact-line">
      <div class="contact-item contact-phone">
        <svg viewBox="0 0 20 20" aria-hidden="true"><circle cx="10" cy="10" r="8.5" fill="none" stroke="var(--blue-deep)" stroke-width="1"/><path d="M7 6 L8.5 6 L9.2 8 L8.2 8.8 C8.8 10.2 9.8 11.2 11.2 11.8 L12 10.8 L14 11.5 L14 13 C10 13.5 6.5 10 7 6 Z" fill="none" stroke="var(--blue-deep)" stroke-width="0.9"/></svg>
        <span>+41 71 555 20 40</span>
      </div>
      <div class="contact-item contact-mail">
        <svg viewBox="0 0 20 20" aria-hidden="true"><circle cx="10" cy="10" r="8.5" fill="none" stroke="var(--blue-deep)" stroke-width="1"/><path d="M5.5 10 L14.5 6 L12 14.5 L9.5 11 Z M9.5 11 L14.5 6" fill="none" stroke="var(--blue-deep)" stroke-width="0.9" stroke-linejoin="round"/></svg>
        <span>info@tavrin.ch</span>
      </div>
      <div class="contact-item contact-address">
        <svg viewBox="0 0 20 20" aria-hidden="true"><circle cx="10" cy="10" r="8.5" fill="none" stroke="var(--blue-deep)" stroke-width="1"/><path d="M10 15 C8 12 6.8 10.3 6.8 8.6 A3.2 3.2 0 0 1 13.2 8.6 C13.2 10.3 12 12 10 15 Z" fill="none" stroke="var(--blue-deep)" stroke-width="0.9"/><circle cx="10" cy="8.6" r="1.1" fill="var(--blue-deep)"/></svg>
        <span>Lindmattstr. 4<span class="divider"></span>9517 Goldach</span>
      </div>
    </footer>
  </main>
</body>
</html>
```